Business Card for Multi-Brand Sportswear Company

We are looking for a business card which represents our company and the multiple brands within it.

The company: Fen Athletics (LTD)
The brands: Fen, TavaPuni, ElmStretch, Grit and Rain

Employees using these cards would be representing Fen Athletics, rather than any of the individual brands. You will see a current design within the uploaded files, to give some inspiration. The actual text of the brands is not necessary, but the logos should be on there is some format.

Our creative minds on this are stretched, so we are looking for someone to make this their own, and show us what a good business card should look like.

We may like to get these printed with spot gloss, so keep that in mind with your designs.

www.fenathletics.co.uk

Industry/Entity Type

Business

Contact Information for Business Card

Leo Pemberton-Hale
Operations Manager
(+44) 1632 960 418
Leo@fenathletics.co.uk
www.fenathletics.co.uk

Font styles to use
Sans Serif
Other font styles liked:
• Eurostile

Colors
ffffff

Requirements
Nice to have
• Dark (black) background

```html
<!DOCTYPE html>
<html lang="en">
<head>
<meta charset="utf-8">
<title>Fen Athletics – Business Card</title>
<link href="https://fonts.googleapis.com/css2?family=Saira:wght@400;500;600&display=swap" rel="stylesheet">
<style>
  :root {
    --stage: #4a4a4a;
    --paper: #ffffff;
    --ink: #111111;
    --text-grey: #555a60;
    --brand-red: #ed1c24;
    --shadow: rgba(0,0,0,0.45);
  }
  * { box-sizing: border-box; margin: 0; padding: 0; }
  html, body { width: 1105px; height: 1200px; overflow: hidden; }
  body {
    background: var(--stage);
    font-family: "Saira", "Helvetica Neue", Arial, sans-serif;
    position: relative;
  }
  .card {
    position: absolute;
    left: 196px;
    width: 720px;
    height: 412px;
    box-shadow: 0 6px 14px var(--shadow);
    overflow: hidden;
  }
  .card--front { top: 146px; background: var(--paper); }
  .card--back { top: 602px; background: var(--brand-red); }

  /* Front */
  .name-band {
    position: absolute; left: 0; top: 56px;
    width: 420px; height: 80px;
    background: var(--ink);
  }
  .name-swoosh { position: absolute; left: 272px; top: 56px; }
  .person { position: absolute; left: 44px; top: 66px; }
  .person__name {
    color: var(--brand-red); font-size: 25px; font-weight: 600; line-height: 1.2;
    letter-spacing: 0.3px;
  }
  .person__role { color: var(--paper); font-size: 18px; font-weight: 400; line-height: 1.3; }

  .address {
    position: absolute; left: 44px; top: 226px;
    color: var(--text-grey); font-size: 18px; line-height: 27px;
  }
  .contacts {
    position: absolute; left: 44px; top: 288px;
    list-style: none; color: var(--text-grey); font-size: 18px;
  }
  .contacts li { display: flex; align-items: center; height: 28px; }
  .contacts svg { width: 17px; height: 17px; margin-right: 11px; flex: none; }

  .front-mark {
    position: absolute; right: 38px; top: 318px; text-align: right;
  }
  .front-mark__name {
    color: var(--ink); font-size: 34px; font-weight: 600; line-height: 1;
  }
  .front-mark__tag {
    color: var(--ink); font-size: 10px; letter-spacing: 2px; margin-top: 5px;
  }

  /* Back */
  .back-mark {
    position: absolute; left: 0; right: 0; top: 128px; text-align: center;
    color: var(--paper);
  }
  .back-mark__name { font-size: 68px; font-weight: 600; line-height: 1; }
  .back-mark__tag { font-size: 15px; letter-spacing: 3px; margin-top: 10px; }

  .brand-row {
    position: absolute; left: 0; right: 0; top: 318px;
    display: flex; justify-content: center; gap: 28px;
    list-style: none; color: var(--paper);
    font-size: 19px; font-weight: 600;
  }
</style>
</head>
<body>

<section class="card card--front" aria-label="Business card front">
  <div class="name-band"></div>
  <svg class="name-swoosh" width="150" height="80" viewBox="0 0 150 80" aria-hidden="true">
    <path d="M150 0 C118 30 98 70 40 80 L0 80 C40 60 78 10 110 0 Z" fill="var(--brand-red)"/>
  </svg>
  <div class="person">
    <p class="person__name">Tom Ashdown</p>
    <p class="person__role">Managing Director</p>
  </div>

  <p class="address">Kettle Yard, Brackendale<br>Holmbridge, HD9 4XQ</p>

  <ul class="contacts">
    <li>
      <svg viewBox="0 0 24 24" aria-hidden="true"><path fill="var(--brand-red)" d="M6.6 10.8a15.1 15.1 0 0 0 6.6 6.6l2.2-2.2a1 1 0 0 1 1-.25 11.4 11.4 0 0 0 3.6.57 1 1 0 0 1 1 1V20a1 1 0 0 1-1 1A17 17 0 0 1 3 4a1 1 0 0 1 1-1h3.5a1 1 0 0 1 1 1c0 1.25.2 2.45.57 3.57a1 1 0 0 1-.25 1z"/></svg>
      +44 (0)1632 960418
    </li>
    <li>
      <svg viewBox="0 0 24 24" aria-hidden="true"><rect x="2" y="5" width="20" height="14" fill="var(--brand-red)"/><path d="M2 5l10 8 10-8" fill="none" stroke="#fff" stroke-width="1.6"/></svg>
      tom@fenathletics.co.uk
    </li>
    <li>
      <svg viewBox="0 0 24 24" aria-hidden="true"><circle cx="12" cy="12" r="10" fill="var(--brand-red)"/><path d="M2 12h20M12 2c3 3 3 17 0 20M12 2c-3 3-3 17 0 20" fill="none" stroke="#fff" stroke-width="1.3"/></svg>
      www.fenathletics.co.uk
    </li>
  </ul>

  <div class="front-mark">
    <p class="front-mark__name">Fen Athletics</p>
    <p class="front-mark__tag">PERFORMANCE WEAR</p>
  </div>
</section>

<section class="card card--back" aria-label="Business card back">
  <div class="back-mark">
    <p class="back-mark__name">Fen Athletics</p>
    <p class="back-mark__tag">PERFORMANCE WEAR</p>
  </div>
  <ul class="brand-row">
    <li>TavaPuni</li>
    <li>ElmStretch</li>
    <li>Grit and Rain</li>
    <li>Fen</li>
  </ul>
</section>

</body>
</html>
```